Mobile Repair Service on location needs a Web Design

We are starting a new mobile device repair service called Handset Haven and our website needs a design!

Hello Designers!
First, we'd like to make clear this is more than a simple web design contest, we want the designers to create an idea. We want someone who can create the whole theme of the service's we provide. We want someone that can help design our visual branding, help us communicate a sentiment. And we are willing to pay for that.

Who are we?
Our company is based in Rotterdam, the Netherlands. We provide different services for all kinds of electronic devices. The kind of services we provide are, among other things, installations of hardware and software and the repair of broken or malfunctioning devices.
We are starting a new service that offers mobile device repairs on location, be it at the home of our customers, their office, or any other place. Just give us the address and we will come to you for the repair job. This is also our main USP. We have multiple skilled engineers who drive trough the country on a daily basis and can be on location within a working day. Repair is done immediately onsite while the customer waits. At this stage we will start with the smartphone product-group within the mobile devices. In a second phase we might also add tablets.
People don't want to be without their phone for weeks because of some parts that needed to be ordered by a repair center they had to sent their phone to. We offer a fully functional mobile repair center in the form of specially customized vans. These vans have all the tools and utilities needed by our engineers to safely repair your mobile device. Your phone is being repaired directly in front of you, the next business-day, on a location you desire.

For this new service we are creating a website called Handset Haven. The website needs a story and matching design and this is where you come in. We are not looking for a simple template design we can get from any place. We need a story. We want you to create an idea, build a unique theme or vision that helps sell the product/service. This goes beyond the design of the website. We need the whole package, the design you are creating needs to have returning elements like icons, color use, images, maybe even characters etc. You name it! There needs to be a common thread in the design so we can reuse elements in, for example, the email templates, the work order or receipt we give to our customers (we may contact the winner of the contest to design these for us as well!).

The name 'Handset Haven' is chosen. Rehab (short for rehabilitate) has a bold and playful tone to it and the design needs to reflect the name. So we're looking for a somewhat playful and cheeky design. Definitely not too serious and definitely modern. We already got a logo that we love and that fit's this description (see attached design documents for the logo). It's bold, powerful and fun. Our web design needs to reflect this as well and has to fit in with our logo.
We would really like it if the design somehow incorporates elements that highlight our unique selling points (repairs on location, we come to you etc.). We would really like some form of story telling in the design. Think clumsy people breaking their phones. Teenagers in tears because they have no access to their friends. People nowadays have the need to always be 'connected'. What happens when your phone is broken or malfunctioning? We're handling tech, we are nerds and a little bit weird, but we're professionals and here to help you with your problem. The sentiment Byte Brigade tries to communicate is something we really like. We're looking for fresh idea's, anything goes!

In an overview all Unique Selling Points of the Handset haven service:
- Professional service on location. Don’t ship to us we will come to you!
- Clear pricing upfront. No hidden cost.
- Next business-day repair.
- Backed by a professional call center open 12 hours a day and open on a Saturday as well
- Backed by a professional repair center with more then 12 years of experience
- Repair is done by certified engineers
- 1 year warranty on the repair

The process:
The main function of our website will be for customers to make a repair request. A customer will visit our website and can make a repair request immediately by going through a 'request-order-flow'. In this flow he or she will need to fill in some forms and can select wich type/model/brand of mobile device he or she has and what parts need to be repaired. After a request is placed we will call the customer back (within an hour) for a short intake and to set a date/time and location. Our engineer will meet the customer at the specified location and will repair the device onsite in one of our mobile repair centers, which is a specialized van equipped with all the tools needed for device restorations.
So in short the steps are:
- Choose your device and repair job
- Place the order
- Get a callback within the hour
- Set date and location
- We will come to you.

Website functionality:
Our website is our main form of communication. So the sentiment we want to communicate needs be reflected in the design. We need a main/front page designed (preferably a long scrolling page design) containing:
1. Customers will be able to request a repair job directly on our website. So there will need to be a prominent button/link at the top of our main page that will bring the customer to this 'request-order-flow'. This is the main flow which needs to be full focus on the front page. All other items are secondary.
2. The general information of who we are and what we do, and why the customer should choose us. Preferably in short bullet-point type keywords/sentences with icons or other visual cues. See our unique selling points to get an idea of the information that will be displayed here.
3. There needs to be a section that will explain the process (see above) of a repair request step-by- step, again in brief short key sentences and with (custom) icons.
4. There needs to be a section that explains to the customer he/she can always contact us if they are not sure what the problem is with their device, and for this reason are not sure what repair request they should order.
5. We want to implement some functionality that display customer ratings or customer reviews. So there needs to be room for some kind of widget of plugin we're going to implement which shows these reviews.
6. A 'For business section' where we will explain all the options we provide for corporate clients.
7. Social media links.
8. There needs to be a menu with buttons that leads to the all sections described in the previous points.

For now, we need a design for our front page. In the second phase, when we have picked our winner, we may ask the winner to design the page(s) for our request workflow as well.

EDIT:
Finally, we have a very specific order in mind for the different segments of our website. We would like you to add some more segments that were not in our original brief as well:

1. Top header with order/request button. (should instantly make clear our main USP, we do repairs on location)
2. Our process
3. Our unique selling points / why choose us
4. The kind of repairs we do (broken screens, broken batteries, water damage, broken camera's, no sound etc.)
5. A 'meet our team' section, where we introduce some of our engineers
6. A 'contact us for any questions' section/
7. Testimonials/user reviews
8. A section where we show key performance indicators
9. 'For businesses' sections
10.'Subscribe for newsletter' field
11. Social media buttons

Industry/Entity Type

It Service

Number of Pages Required

1 page

Font styles to use
Sans Serif

Requirements
Must have
• a main/front page, design only
• custom icons/images for banners, adverts online and in print (high res)
Nice to have
• Storytelling in our design.
• Design that fits with our brand new logo.
• Elements like icons to have a flat design.
• Keep in mind that the website will need to be responsive when designing! (Ideally provide an example of the mobile design as well)
• Create a fun and trustworthy feeling.

```html
<!DOCTYPE html>
<html lang="en">
<head>
<meta charset="utf-8">
<title>Handset Haven – Mobile Repair On Location</title>
<link href="https://fonts.googleapis.com/css2?family=Roboto:ital,wght@0,300;0,400;0,500;0,700;0,900;1,400&display=swap" rel="stylesheet">
<style>
:root{
  --brand:#d9432a;
  --brand-dark:#c33a22;
  --ink:#444;
  --ink-soft:#666;
  --line:#dcdcdc;
  --band:#ececec;
  --nav-top:#5b5b5b;
  --nav-bottom:#3d3d3d;
  --white:#fff;
}
*{box-sizing:border-box;margin:0;padding:0}
html,body{width:778px;height:1200px;overflow:hidden;background:var(--white)}
body{position:relative;font-family:'Roboto',Arial,sans-serif;color:var(--ink)}
.abs{position:absolute}

/* header */
.brand{left:65px;top:12px;display:flex;align-items:center;gap:8px}
.brand-dot{width:34px;height:34px;border-radius:50%;background:var(--brand)}
.brand-name{font-weight:900;font-size:17px;line-height:16px;color:#333;letter-spacing:.3px}
.brand-tag{font-size:6px;color:#555;margin-top:3px;font-weight:500}
.search{left:296px;top:26px;width:249px;height:24px;border:1px solid var(--line);font-size:8px;color:#999;padding:7px 10px;display:flex;justify-content:space-between}
.call{left:575px;top:19px;display:flex;gap:9px;align-items:center}
.call-icon{width:32px;height:32px;border-radius:50%;background:var(--brand);display:flex;align-items:center;justify-content:center}
.call-label{font-size:8px;color:#555}
.call-number{font-size:13px;color:var(--brand);margin-top:3px}

/* nav */
.nav{left:0;top:73px;width:778px;height:29px;background:linear-gradient(var(--nav-top),var(--nav-bottom))}
.nav ul{position:absolute;left:66px;top:0;height:29px;display:flex;list-style:none}
.nav li{height:29px;display:flex;align-items:center;justify-content:center;font-size:7.5px;font-weight:500;color:var(--white);border-right:1px solid #333}
.nav li.active{background:var(--brand)}

/* hero */
.hero{left:65px;top:111px;width:649px;height:278px;border:1px solid var(--line);padding:3px;background:var(--white)}
.hero-photo{width:100%;height:100%;background:linear-gradient(120deg,#cfd3d6,#8a8e90 40%,#6f7a5c 70%,#d9c0ad)}
.hero-caption{left:68px;top:283px;width:298px;height:69px;background:var(--brand);color:var(--white);font-size:12.5px;font-weight:500;line-height:20px;padding:14px 16px}
.dots{left:376px;top:374px;display:flex;gap:3px}
.dots span{width:5px;height:5px;border-radius:50%;background:#ccc}
.dots span:first-child{background:var(--brand)}

/* steps */
.step{top:413px;width:123px;height:114px;border:1px solid var(--line);text-align:center;font-size:8px;line-height:13px;color:#555}
.step svg{display:block;margin:16px auto 10px}

/* usp */
.usp-photo{left:65px;top:570px;width:237px;height:183px;border:1px solid var(--line);padding:4px}
.usp-photo div{width:100%;height:100%;background:linear-gradient(135deg,#b8c6cc,#e2e6e8 50%,#8fa3ad)}
.usp-title{left:337px;top:567px;font-size:16px;color:#444}
.usp-item{display:flex;gap:10px;font-size:8px;line-height:15.5px;color:#555;width:185px}
.usp-item svg{flex:none;margin-top:1px}

/* band */
.band{left:0;top:794px;width:778px;height:223px;background:var(--band);border-top:1px solid #ddd;border-bottom:1px solid #ddd}
.h2{font-size:16px;color:#444}
.about-text{left:65px;top:864px;width:330px;font-size:7.4px;line-height:16.6px;color:#555}
.btn{left:65px;top:958px;width:76px;height:25px;background:var(--brand);color:var(--white);font-size:8px;font-weight:500;display:flex;align-items:center;justify-content:center}
.avatar{left:442px;top:871px;width:90px;height:90px;border-radius:50%;background:radial-gradient(#d8d8d8,#b9b9b9);border:3px solid var(--white)}
.review-name{left:552px;top:872px;font-size:9px;color:var(--brand)}
.review-role{left:552px;top:887px;font-size:7.5px;color:#666}
.review-quote{left:553px;top:903px;width:160px;font-size:7.2px;line-height:15px;font-style:italic;color:#666}
.arrows{left:697px;top:872px;font-size:9px;color:#aaa;letter-spacing:4px}

/* footer */
.foot-brand{left:70px;top:1062px;display:flex;align-items:center;gap:9px}
.foot-brand .brand-dot{width:46px;height:46px}
.foot-brand .brand-name{font-size:21px;line-height:21px}
.foot-col h3{font-size:11px;font-weight:400;color:#444;margin-bottom:10px}
.foot-col p{font-size:7px;line-height:17px;color:#555}
.foot-col .hi{color:var(--brand)}
.socials{display:flex;gap:3px;margin-top:6px}
.socials span{width:20px;height:20px;border-radius:50%;background:var(--brand)}
.rule{left:0;top:1166px;width:778px;height:1px;background:#e2e2e2}
.copy{left:0;top:1177px;width:778px;text-align:center;font-size:7px;color:#555}
</style>
</head>
<body>

<header>
  <div class="abs brand">
    <span class="brand-dot"></span>
    <div><div class="brand-name">HANDSET<br>HAVEN</div><div class="brand-tag">We will come to you!</div></div>
  </div>
  <div class="abs search"><span>Search by keyword</span>
    <svg width="9" height="9" viewBox="0 0 10 10"><circle cx="4" cy="4" r="3.2" fill="none" stroke="#aaa"/><path d="M6.4 6.4 9 9" stroke="#aaa"/></svg>
  </div>
  <div class="abs call">
    <span class="call-icon"><svg width="14" height="14" viewBox="0 0 24 24"><path fill="#fff" d="M6.6 10.8a15 15 0 0 0 6.6 6.6l2.2-2.2c.3-.3.7-.4 1-.2 1.1.4 2.3.6 3.6.6.6 0 1 .4 1 1V20c0 .6-.4 1-1 1A17 17 0 0 1 3 4c0-.6.4-1 1-1h3.5c.6 0 1 .4 1 1 0 1.3.2 2.5.6 3.6.1.3 0 .7-.2 1z"/></svg></span>
    <div><div class="call-label">Get in touch:</div><div class="call-number">( 555 ) 214 - 7730</div></div>
  </div>
</header>

<nav class="abs nav">
  <ul>
    <li class="active" style="width:73px">HOME</li>
    <li style="width:97px">ABOUT US</li>
    <li style="width:91px">SERVICES</li>
    <li style="width:73px">USP</li>
    <li style="width:108px">PLACE ORDER</li>
    <li style="width:109px">TESTIMONIALS</li>
    <li style="width:96px">CONTACT US</li>
  </ul>
</nav>

<section>
  <div class="abs hero"><div class="hero-photo" role="img" aria-label="Close-up of hands fitting a new display onto a phone circuit board with tweezers"></div></div>
  <div class="abs hero-caption">PROFESSIONAL SERVICE ON LOCATION.<br>DON'T SHIP TO US WE WILL COME TO YOU!</div>
  <div class="abs dots"><span></span><span></span><span></span><span></span></div>
</section>

<section>
  <div class="abs step" style="left:65px">
    <svg width="34" height="38" viewBox="0 0 34 38" fill="none" stroke="#d9432a" stroke-width="1.6"><rect x="10" y="2" width="18" height="32" rx="2"/><path d="M4 30l12-12M16 18a4 4 0 1 1 5-5l-3 1-1 3z"/></svg>
    Choose your device<br>and repair job</div>
  <div class="abs step" style="left:196px">
    <svg width="38" height="38" viewBox="0 0 38 38" fill="none" stroke="#d9432a" stroke-width="1.6"><path d="M4 20h9l2 4h8l2-4h9v13H4z"/><path d="M4 20l5-8h4M34 20l-5-8h-4M19 3v15M14 13l5 5 5-5"/></svg>
    Place the order</div>
  <div class="abs step" style="left:328px">
    <svg width="38" height="38" viewBox="0 0 38 38" fill="none" stroke="#d9432a" stroke-width="1.8"><circle cx="24" cy="13" r="9"/><path d="M24 8v5h4"/><path d="M5 14c0 10 8 19 18 19l2-5-5-2-2 3c-3-1-6-5-7-8l3-2-2-5z" fill="#d9432a"/></svg>
    Get a callback within<br>the hour</div>
  <div class="abs step" style="left:460px">
    <svg width="38" height="38" viewBox="0 0 38 38" fill="none" stroke="#d9432a" stroke-width="1.5"><path d="M19 26s-9-9-9-14a9 9 0 0 1 18 0c0 5-9 14-9 14z"/><circle cx="19" cy="12" r="3.5"/><path d="M10 20l-7 3-2 12 11-4 7 3 7-3 11 4-2-12-7-3"/></svg>
    Set date and<br>location</div>
  <div class="abs step" style="left:592px">
    <svg width="42" height="38" viewBox="0 0 42 38" fill="none" stroke="#d9432a" stroke-width="1.5"><circle cx="16" cy="11" r="7"/><path d="M3 34c0-9 6-14 13-14 3 0 5 1 7 2M3 34h18"/><circle cx="31" cy="27" r="4"/><circle cx="31" cy="27" r="8" stroke-dasharray="3 2"/></svg>
    We will come to<br>you.</div>
</section>

<section>
  <div class="abs usp-photo"><div role="img" aria-label="Technician in gloves repairing an opened smartphone with a screwdriver"></div></div>
  <h2 class="abs usp-title">USP</h2>

  <div class="abs usp-item" style="left:337px;top:606px">
    <svg width="16" height="18" viewBox="0 0 16 18"><path fill="#d9432a" d="M8 1a6 6 0 0 0-6 6c0 4 6 10 6 10s6-6 6-10a6 6 0 0 0-6-6zm0 8a2 2 0 1 1 0-4 2 2 0 0 1 0 4z"/></svg>
    <span>Professional service on location. Don't ship to us we will come to you!</span></div>
  <div class="abs usp-item" style="left:337px;top:649px">
    <svg width="16" height="18" viewBox="0 0 16 18"><path fill="#d9432a" d="M2 2h7l6 7-7 8-6-7z"/><circle cx="5.5" cy="5.5" r="1.3" fill="#fff"/></svg>
    <span>Clear pricing upfront. No hidden cost.</span></div>
  <div class="abs usp-item" style="left:337px;top:677px">
    <svg width="16" height="18" viewBox="0 0 16 18" stroke="#d9432a" stroke-width="2"><path d="M2 16L14 3M3 3l11 13"/></svg>
    <span>Next business-day repair.</span></div>
  <div class="abs usp-item" style="left:337px;top:705px;width:175px">
    <svg width="16" height="18" viewBox="0 0 16 18" fill="none" stroke="#d9432a" stroke-width="1.4"><path d="M3 10V8a5 5 0 0 1 10 0v2"/><rect x="1.5" y="9" width="3" height="5" rx="1"/><rect x="11.5" y="9" width="3" height="5" rx="1"/><path d="M13 14c0 2-2 3-5 3"/></svg>
    <span>Backed by a professional call center open 12 hours a day and open on a Saturday as</span></div>

  <div class="abs usp-item" style="left:544px;top:606px">
    <svg width="22" height="20" viewBox="0 0 22 20" fill="none" stroke="#d9432a" stroke-width="1.2"><circle cx="11" cy="10" r="3"/><circle cx="11" cy="2.5" r="1.8"/><circle cx="11" cy="17.5" r="1.8"/><circle cx="3" cy="6" r="1.8"/><circle cx="19" cy="6" r="1.8"/><circle cx="3" cy="14" r="1.8"/><circle cx="19" cy="14" r="1.8"/></svg>
    <span>Backed by a professional repair center with more then 12 years of experience</span></div>
  <div class="abs usp-item" style="left:547px;top:649px">
    <svg width="16" height="18" viewBox="0 0 16 18" fill="none" stroke="#d9432a" stroke-width="1.2"><path d="M2 1h9l3 3v13H2z"/><path d="M5 6h6M5 9h6M5 12h3"/><circle cx="12" cy="14" r="2.5"/></svg>
    <span>Repair is done by certified engineers</span></div>
  <div class="abs usp-item" style="left:547px;top:677px">
    <svg width="16" height="18" viewBox="0 0 16 18" fill="none" stroke="#d9432a" stroke-width="1.3"><circle cx="8" cy="7" r="5.5"/><circle cx="8" cy="7" r="2.5"/><path d="M4 11l-2 6 3-1 2 2 1-5M12 11l2 6-3-1-2 2"/></svg>
    <span>1 year warranty on the repair</span></div>
</section>

<section class="abs band">
</section>
<h2 class="abs h2" style="left:65px;top:833px">Who are we?</h2>
<p class="abs about-text">Our company is based in Rotterdam, the Netherlands. We provide different services for all kinds of electronic devices. The kind of services we provide are, among other things, installations of hardware and software and the repair of broken or malfunctioning devices. We are starting a new service that offers mobile device repairs on location, be it at the home of our customers, their office, or any other place...</p>
<div class="abs btn">LEARN MORE</div>

<h2 class="abs h2" style="left:438px;top:829px">What our client’s say</h2>
<div class="abs avatar" role="img" aria-label="Portrait photo of the reviewing client"></div>
<div class="abs review-name">Marten Vries</div>
<div class="abs review-role">Business man</div>
<p class="abs review-quote">Lorem Ipsum is simply dummy text of the printing and typesetting industry. Lorem Ipsum has been the industry's standard dummy text ever since the 1500s</p>
<div class="abs arrows">‹ ›</div>

<footer>
  <div class="abs foot-brand">
    <span class="brand-dot"></span>
    <div><div class="brand-name">HANDSET<br>HAVEN</div><div class="brand-tag" style="font-size:7px">We will come to you!</div></div>
  </div>
  <div class="abs foot-col" style="left:290px;top:1039px">
    <h3>Welcome</h3>
    <p>Home<br>About<br>Services<br>USP<br>Testimonials</p>
  </div>
  <div class="abs foot-col" style="left:420px;top:1039px">
    <h3>Contact Info</h3>
    <p>120 Street name, City name,<br>Country name : 985666<br>Phone : <span class="hi">( 555 ) 214 - 7730</span><br>Email : <span class="hi">info@handsethaven.com</span></p>
  </div>
  <div class="abs foot-col" style="left:589px;top:1039px">
    <h3>Follow us</h3>
    <p>Connect with our social network</p>
    <div class="socials"><span aria-label="Social link"></span><span aria-label="Social link"></span><span aria-label="Social link"></span><span aria-label="Social link"></span><span aria-label="Social link"></span></div>
  </div>
  <div class="abs rule"></div>
  <div class="abs copy">Copyright © 2017. Handset Haven. All Rights Reserved</div>
</footer>

</body>
</html>
```